Vellmore Family Law, legal technician needs a website and design

I need a website for a family law practice. I specialize in collaborative law, unbundled services, and mediation. The website must contain my company logo (file attached), and the website must be a mixture of my personality and my profession. I have attached additional information to explain my personality and profession.

Target Market(s)

Lower through middle-class (income level up to $200,000 per year)

Coding

Coded - Design and coding required

Number of Pages Required

1 page

Requirements
Must have
• Must have enough pages to cover required content. I submitted below some content about the collaborative law process. All of the content is not necessary. However, the website must have enough content to clearly describe the services I offer. Use your professionalism and judgment regarding font, font size, etc.

```html
<!DOCTYPE html>
<html lang="en">
<head>
<meta charset="utf-8">
<title>About Daren – Vellmore Family Law</title>
<link rel="stylesheet" href="https://fonts.googleapis.com/css2?family=Cinzel:wght@700&family=Ubuntu:wght@400;500&family=Open+Sans:wght@400;600&display=swap">
<style>
:root{
  --ink:#1b1735;
  --gold:#a89a3c;
  --olive:#868309;
  --lime:#a6ab3b;
  --lime-soft:#c9c95a;
  --dark:#1b1b1b;
  --darker:#3a3a3a;
  --text:#333;
  --line:#999;
}
*{box-sizing:border-box;margin:0;padding:0}
html,body{width:1200px;height:2702px;overflow:hidden}
body{position:relative;background:#fff;font-family:"Open Sans",sans-serif;color:var(--text)}
.abs{position:absolute}

/* header */
.site-header{left:0;top:0;width:1200px;height:98px;background:#fff;box-shadow:0 3px 6px rgba(0,0,0,.18);z-index:2}
.brand{left:140px;top:24px;display:flex;align-items:center;gap:12px}
.brand-mark{width:40px;height:40px;background:var(--gold)}
.brand-name{font-family:"Cinzel",serif;font-weight:700;color:var(--gold);font-size:17px;line-height:19px}
.main-nav{left:368px;top:41px;display:flex;gap:11px;font-family:"Ubuntu",sans-serif;font-size:12px;font-weight:500;color:#111}
.social{left:906px;top:37px;display:flex;gap:6px}
.social span{width:27px;height:27px;border-radius:50%;background:var(--gold)}

/* hero */
.hero{left:0;top:98px;width:1200px;height:314px;background:linear-gradient(180deg,#dcdadb 0%,#e4e2e3 60%,#d2d0cf 100%)}
.hero-title{left:0;top:223px;width:1200px;text-align:center;font-family:"Cinzel",serif;font-weight:700;font-size:50px;color:var(--ink);letter-spacing:1px}

/* about */
.portrait-frame{left:132px;top:508px;width:383px;height:565px;border:6px solid var(--olive);border-right:none;border-bottom:none}
.portrait{left:138px;top:514px;width:383px;height:565px;background:linear-gradient(160deg,#c9c8c2,#8b8a87 45%,#3c4150 75%,#6c6860)}
.about-text{left:548px;top:505px;width:512px;font-size:9.6px;line-height:18px;text-align:justify}
.about-text h2{font-family:"Cinzel",serif;font-weight:700;font-size:27px;color:var(--ink);line-height:36px}
.about-text .rule{width:95px;height:2px;background:var(--gold);margin:6px 0 16px}
.about-text h3{font-family:"Ubuntu",sans-serif;font-weight:500;font-size:15px;color:#111;margin:14px 0 8px}
.about-text p{margin-bottom:12px}
.about-text p.tight{margin-bottom:0}

/* credentials */
.creds{left:138px;top:1158px;width:923px;height:234px;border:1px solid var(--line)}
.creds-photo{left:6px;top:6px;width:262px;height:221px;background:linear-gradient(180deg,#3a3735,#5d4c42 55%,#22252e)}
.creds-body{left:296px;top:22px;font-size:11px;line-height:21.5px}
.creds-body h3{font-family:"Ubuntu",sans-serif;font-weight:500;font-size:18px;color:#111;margin-bottom:8px}
.creds-body ul{list-style:none}
.creds-body li{display:flex;align-items:center;gap:8px}

/* process */
.process{left:0;top:1440px;width:1200px;height:682px;background:linear-gradient(180deg,#fff 0%,#f4f2ee 45%,#e3ddd0 100%)}
.process h2{position:absolute;left:0;top:68px;width:1200px;text-align:center;font-family:"Cinzel",serif;font-weight:700;font-size:28px;color:var(--ink)}
.process .lead{position:absolute;left:150px;top:113px;width:900px;text-align:center;font-size:11px;line-height:21.5px}
.cta{position:absolute;left:365px;top:173px;width:471px;height:46px;background:var(--lime);display:flex;align-items:center;justify-content:center;font-family:"Ubuntu",sans-serif;font-size:13px;color:#111;gap:5px}
.cta em{font-style:normal;color:#3f4010}
.video{position:absolute;left:259px;top:257px;width:682px;height:351px;border:2px solid #eee;box-shadow:0 0 6px rgba(0,0,0,.25);background:linear-gradient(180deg,#8fa6a4,#6c8483 70%,#8a8478)}
.play{position:absolute;left:310px;top:155px;width:64px;height:42px;border-radius:8px;background:#111}
.controls{position:absolute;left:0;bottom:0;width:100%;height:22px;background:linear-gradient(#f2f2f2,#cfcfcf);display:flex;align-items:center;gap:8px;padding:0 8px;font-size:8px;color:#333}
.controls .bar{flex:1;height:4px;background:#aaa;border-radius:2px}

/* footer */
.footer-line{left:0;top:2122px;width:1200px;height:3px;background:var(--lime-soft)}
.site-footer{left:0;top:2125px;width:1200px;height:516px;background:var(--dark)}
.footer-brand{left:140px;top:2283px;display:flex;align-items:center;gap:14px}
.footer-brand .brand-mark{width:56px;height:56px}
.footer-brand .brand-name{font-size:24px;line-height:27px}
.contact-item{left:137px;display:flex;align-items:center;gap:12px;color:#fff}
.contact-item .dot{width:40px;height:40px;border-radius:50%;background:var(--lime-soft);display:flex;align-items:center;justify-content:center}
.contact-item small{display:block;font-family:"Ubuntu",sans-serif;font-weight:500;font-size:12px}
.contact-item b{font-family:"Ubuntu",sans-serif;font-weight:400;font-size:17px}
.contact-box{left:503px;top:2198px;width:558px;height:406px;background:linear-gradient(135deg,#8c8a3e,#948f45 50%,#85823a)}
.contact-box h2{position:absolute;left:35px;top:55px;font-family:"Cinzel",serif;font-weight:700;font-size:26px;color:#fff}
.field{position:absolute;background:#fff;font-size:11.5px;color:#555;padding:15px 12px}
.submit{position:absolute;left:35px;top:299px;width:103px;height:48px;background:#161616;color:#fff;font-family:"Ubuntu",sans-serif;font-size:14px;display:flex;align-items:center;justify-content:center}
.copyright{left:0;top:2641px;width:1200px;height:61px;background:var(--darker);color:#eee;font-family:"Ubuntu",sans-serif;font-size:11px;display:flex;align-items:center;justify-content:center}
</style>
</head>
<body>

<header class="abs site-header">
  <div class="abs brand"><span class="brand-mark"></span><span class="brand-name">Vellmore<br>Family Law</span></div>
  <nav class="abs main-nav"><span>HOME</span><span>ABOUT</span><span>MEDIATION</span><span>UNBUNDLED SERVICES</span><span>COLLABORATIVE PROCESS</span><span>CONTACT</span></nav>
  <div class="abs social"><span></span><span></span><span></span><span></span><span></span></div>
</header>

<section class="abs hero" role="img" aria-label="Faded city skyline at dusk"></section>
<h1 class="abs hero-title">ABOUT DAREN</h1>

<div class="abs portrait-frame"></div>
<div class="abs portrait" role="img" aria-label="Portrait of Daren Vellmore in a suit, seated outdoors"></div>

<article class="abs about-text">
  <h2>ABOUT DAREN</h2>
  <div class="rule"></div>
  <p>My name is Daren Vellmore, and I am the owner of Vellmore Family Law, Legal Technician in King County, Washington, where I practice exclusively in Superior Court. I am passionate about helping people resolve their family law disputes.</p>
  <h3>Journey to Practicing Law:</h3>
  <p>I became interested in family law after struggling personally with a child support modification. As I completed my forms, there were many errors needing correction. Every law clerk I asked for assistance told me they could not give legal advice and consult an attorney. I could not afford an attorney, and at that time, there were few, if any, pro bono (free) services available to low-income persons like me. After years of trial and error, I finally got a judge to sign my orders.</p>
  <p>While preparing my child support modification, I spoke to many African American men with children in similar situations (court-ordered child support based on imputed and speculative income standards). African-American men struggling through the legal system is the impetus for opening a collaborative law practice.</p>
  <h3>Mission:</h3>
  <p>At Vellmore Family Law, our mission is to provide an alternative means to the traditional and costly approach to resolve family matters through the collaborative law process.</p>
  <h3>Collaborative Law Process:</h3>
  <p class="tight">The parties create an agreement without going to trial by negotiating a just and equitable agreement where both parties are satisfied with the outcome and in the child's best interest.</p>
  <p class="tight">Today, I am honored to be the sole practitioner at Vellmore Family Law, Legal Technician. I coordinate with other professionals, including attorneys, financial consultants, guardian ad litem, and family therapists, to identify an equitable and just agreement for my clients. I aim to help families and individuals in need of legal assistance, giving them an alternative to the inherent costly traditional courtroom battles with a collaborative law approach to dispute resolution.</p>
</article>

<section class="abs creds">
  <div class="abs creds-photo" role="img" aria-label="Headshot of Daren Vellmore"></div>
  <div class="abs creds-body">
    <h3>Education &amp; Creditials:</h3>
    <ul>
      <li><svg width="10" height="10" viewBox="0 0 10 10"><path d="M1 5l3 3 5-7" fill="none" stroke="#868309" stroke-width="2"/></svg>LLLT, Cascade State University, School of Law</li>
      <li><svg width="10" height="10" viewBox="0 0 10 10"><path d="M1 5l3 3 5-7" fill="none" stroke="#868309" stroke-width="2"/></svg>B.A. Information Technology Administration Management, Eastmont University</li>
      <li><svg width="10" height="10" viewBox="0 0 10 10"><path d="M1 5l3 3 5-7" fill="none" stroke="#868309" stroke-width="2"/></svg>A.S. Paralegal Studies, Riverside Community College</li>
      <li><svg width="10" height="10" viewBox="0 0 10 10"><path d="M1 5l3 3 5-7" fill="none" stroke="#868309" stroke-width="2"/></svg>A.A. Diversity in Global Studies, Riverside Community College</li>
    </ul>
    <p>Bar Admissions</p>
    <p>? Washington State</p>
    <p>(insert hyperlink) (insert hyperlink)</p>
  </div>
</section>

<section class="abs process">
  <h2>COLLABORATIVE PROCESS</h2>
  <p class="lead">As you can see, there are plenty of reasons to consider Collaborative practice. It will help you to peacefully resolve conflicts and move through the legal process as efficiently and cost-effectively as possible.</p>
  <div class="cta">Want to save money on court fees? <em>Consider the collaborative approach</em></div>
  <div class="video" role="img" aria-label="Animated explainer video still: office scene with a presenter">
    <div class="play"><svg width="64" height="42" viewBox="0 0 64 42"><path d="M26 11l16 10-16 10z" fill="#fff"/></svg></div>
    <div class="controls"><svg width="10" height="10" viewBox="0 0 10 10"><path d="M2 1l7 4-7 4z" fill="#444"/></svg><span>0:00 / 0:00</span><span class="bar"></span></div>
  </div>
</section>

<div class="abs footer-line"></div>
<footer class="abs site-footer"></footer>
<div class="abs brand footer-brand"><span class="brand-mark"></span><span class="brand-name">Vellmore<br>Family Law</span></div>

<div class="abs contact-item" style="top:2419px">
  <span class="dot"><svg width="18" height="18" viewBox="0 0 24 24"><path d="M6.6 10.8a15 15 0 006.6 6.6l2.2-2.2c.3-.3.7-.4 1-.2 1.1.4 2.3.6 3.6.6.6 0 1 .4 1 1V20c0 .6-.4 1-1 1A17 17 0 013 4c0-.6.4-1 1-1h3.5c.6 0 1 .4 1 1 0 1.3.2 2.5.6 3.6.1.3 0 .7-.2 1z" fill="#fff"/></svg></span>
  <div><small>CALL US AT:</small><b>+ 123 456 7890</b></div>
</div>
<div class="abs contact-item" style="top:2493px">
  <span class="dot"><svg width="18" height="18" viewBox="0 0 24 24"><rect x="3" y="6" width="18" height="12" rx="1" fill="none" stroke="#fff" stroke-width="1.8"/><path d="M3 7l9 6 9-6" fill="none" stroke="#fff" stroke-width="1.8"/></svg></span>
  <div><small>MAIL US AT:</small><b>info@vellmorefamily.com</b></div>
</div>

<section class="abs contact-box">
  <h2>CONTACT US</h2>
  <div class="field" style="left:35px;top:104px;width:241px;height:47px">First Name</div>
  <div class="field" style="left:282px;top:104px;width:241px;height:47px">Last Name</div>
  <div class="field" style="left:35px;top:159px;width:241px;height:47px">Email</div>
  <div class="field" style="left:282px;top:159px;width:241px;height:47px">Phone</div>
  <div class="field" style="left:35px;top:213px;width:488px;height:75px">Message</div>
  <div class="submit">SUBMIT</div>
</section>

<div class="abs copyright">Copyrights @ 2021 Vellmore Family Law. All Rights Reserved.</div>

</body>
</html>
```